Tellmora Corporate Stationery

Look for design of all new corporate stationery for an existing insurance broking business that is going through a redesign and move from older partners to younger family members. New Logo is attached. Company is Brisbane based.
Colours in the Logo is Hex #43bed8 and website features a lot of hex #17b8d8. Website front page "A plan to protect you" - headline. "Professional and Individual advice to protect your greatest assets" - tagline.

Stationery required: Business Cards, Letter head, Thank-you cards, Birthday cards, Presentation folders, With Compliment slips and a powerpoint template. We also would like to send a card to all customers with the something along of the lines of "something new".

Target Market(s)

Customers of Insurance business looking at superannuation, life and income protection insurance, investment advice and wills

Industry/Entity Type

Insurance Broker

Font styles to use
Other font styles liked:
• same as logo

Requirements
Must have
• The above designs for new stationery for the new business including:
• Business Cards, Letter head, Thank-you cards, Birthday cards, Presentation folders, With Compliment slips and a powerpoint template. We also would like to send a card to all customers with the something along of the lines of "something new".
Nice to have
• It is a new look - long time family business being passed to next generation - big focus on advice for YOU, individual advice etc..

```html
<!DOCTYPE html>
<html lang="en">
<head>
<meta charset="utf-8">
<title>Tellmora Business Card</title>
<link rel="stylesheet" href="https://fonts.googleapis.com/css2?family=Open+Sans:wght@400;600;700&display=swap">
<style>
  :root {
    --brand-blue: #43bed8;
    --brand-blue-deep: #17b8d8;
    --back-dark: #2aa9c6;
    --ink-gray: #6f6f71;
    --panel-gray: #6b6b6d;
    --panel-gray-light: #9a9a9c;
    --paper: #ffffff;
    --stage: #e9ecee;
  }
  * { margin: 0; padding: 0; box-sizing: border-box; }
  html, body {
    width: 1200px;
    height: 843px;
    overflow: hidden;
    background: var(--stage);
    font-family: "Open Sans", Arial, sans-serif;
  }
  .sheet {
    position: relative;
    width: 1200px;
    height: 843px;
    display: flex;
    align-items: center;
    justify-content: center;
    gap: 40px;
  }
  .card {
    position: relative;
    width: 540px;
    height: 309px;
    overflow: hidden;
    box-shadow: 0 6px 18px rgba(0,0,0,0.18);
  }
  .card-shapes {
    position: absolute;
    inset: 0;
    width: 100%;
    height: 100%;
  }

  /* Back side */
  .card-back {
    background: linear-gradient(135deg, var(--brand-blue) 0%, var(--brand-blue-deep) 55%, var(--back-dark) 100%);
  }
  .back-identity {
    position: absolute;
    right: 34px;
    bottom: 34px;
    text-align: left;
    color: var(--paper);
  }
  .back-name {
    font-size: 27px;
    font-weight: 600;
    letter-spacing: 1px;
    line-height: 1;
    text-transform: uppercase;
  }
  .back-group {
    font-size: 12px;
    font-weight: 600;
    letter-spacing: 1.5px;
    text-transform: uppercase;
    margin-top: 2px;
  }
  .back-web {
    font-size: 13px;
    letter-spacing: 2px;
    margin-top: 2px;
  }

  /* Front side */
  .card-front { background: var(--paper); }
  .front-brand {
    position: absolute;
    left: 34px;
    top: 32px;
    display: flex;
    align-items: center;
    gap: 10px;
  }
  .brand-dot {
    width: 26px;
    height: 26px;
    border-radius: 50%;
    background: var(--panel-gray-light);
  }
  .brand-name {
    color: var(--brand-blue);
    font-weight: 600;
    font-size: 17px;
    letter-spacing: 1px;
    line-height: 1.05;
    text-transform: uppercase;
  }
  .brand-name small {
    display: block;
    font-size: 10px;
    letter-spacing: 1.4px;
  }
  .holder {
    position: absolute;
    left: 34px;
    top: 92px;
  }
  .holder-name {
    color: var(--brand-blue);
    font-weight: 700;
    font-size: 15px;
    letter-spacing: 0.5px;
    text-transform: uppercase;
  }
  .holder-title {
    color: var(--ink-gray);
    font-size: 12px;
  }
  .contact-list {
    position: absolute;
    right: 16px;
    bottom: 14px;
    list-style: none;
    color: var(--paper);
    font-size: 12.5px;
    line-height: 19px;
    text-align: right;
  }
  .contact-list li {
    display: flex;
    align-items: center;
    justify-content: flex-end;
    gap: 8px;
  }
  .contact-icon {
    width: 11px;
    height: 11px;
    flex: none;
  }
</style>
</head>
<body>
<main class="sheet">

  <section class="card card-back" aria-label="Business card, back">
    <div class="back-identity">
      <div class="back-name">Tellmora</div>
      <div class="back-group">Financial Group</div>
      <div class="back-web">www.tellmora.com</div>
    </div>
  </section>

  <section class="card card-front" aria-label="Business card, front">
    <svg class="card-shapes" viewBox="0 0 540 309" preserveAspectRatio="none" aria-hidden="true">
      <defs>
        <linearGradient id="panelShade" x1="0" y1="0" x2="1" y2="1">
          <stop offset="0" stop-color="#8d8d8f"/>
          <stop offset="1" stop-color="#5f5f61"/>
        </linearGradient>
      </defs>
      <polygon points="0,272 540,158 540,309 0,309" fill="url(#panelShade)"/>
      <polygon points="0,265 540,150 540,158 0,272" fill="#43bed8"/>
    </svg>

    <div class="front-brand">
      <span class="brand-dot"></span>
      <div class="brand-name">Tellmora<small>Financial Group</small></div>
    </div>

    <div class="holder">
      <div class="holder-name">Daniel Hart</div>
      <div class="holder-title">CEO/Founder</div>
    </div>

    <ul class="contact-list">
      <li>312 580 4417
        <svg class="contact-icon" viewBox="0 0 12 12"><path d="M2 1l2.5 0 1 3-1.5 1a7 7 0 0 0 3 3l1-1.5 3 1V10a1 1 0 0 1-1 1A10 10 0 0 1 1 2a1 1 0 0 1 1-1z" fill="#43bed8"/></svg>
      </li>
      <li>745 219 8630
        <svg class="contact-icon" viewBox="0 0 12 12"><rect x="3" y="0.5" width="6" height="11" rx="1" fill="none" stroke="#43bed8" stroke-width="1.4"/></svg>
      </li>
      <li>598 302 7715
        <svg class="contact-icon" viewBox="0 0 12 12"><rect x="1" y="4" width="10" height="7" rx="1" fill="#43bed8"/><rect x="3" y="1" width="6" height="4" fill="none" stroke="#43bed8" stroke-width="1.2"/></svg>
      </li>
      <li>hello@tellmora.com
        <svg class="contact-icon" viewBox="0 0 12 12"><rect x="0.5" y="2.5" width="11" height="7" fill="#43bed8"/><path d="M0.5 2.5L6 7l5.5-4.5" fill="none" stroke="#ffffff" stroke-width="0.9"/></svg>
      </li>
      <li>www.tellmora.com
        <svg class="contact-icon" viewBox="0 0 12 12"><rect x="0.5" y="1.5" width="11" height="8" rx="1" fill="#43bed8"/><rect x="4" y="10" width="4" height="1.5" fill="#43bed8"/></svg>
      </li>
      <li>214 Wattle Grove Road, Brisbane, QLD 4000
        <svg class="contact-icon" viewBox="0 0 12 12"><circle cx="6" cy="6" r="5.5" fill="#43bed8"/><circle cx="6" cy="5" r="1.8" fill="#ffffff"/></svg>
      </li>
    </ul>
  </section>

</main>
</body>
</html>
```